Label design for one hand cream.

The name of the company is Quelvia. We are launching a hand cream that is also an immediate cleaner without any water. It removes dirt from your hands without using water. After the use, your hands will be soft. It could be used in your feet too.

The company logo reminds of plants, nature and we would like this approach too. Please, remove the words "Produtos Naturais" from the logo.

Reason: Not enough designs. Bad ones

Reason: I have not received one design that pleased us.

Target Market(s)

Public in General. Mostly women.

Industry/Entity Type

Cosmetics

Font styles to use
Sans Serif

Colors
33b8a4
00a990
9bcb3c
acd036
fee087
fece3e
ffc214
fbed22
fbee3e

Requirements
Must have
• You must use the words in the label. Please, see the file attached but just use the WORDS, not the same structure. The image must be 15,5cm high and 7,5 cm wide.
• Use a darker green and some GOLDEN lines or details. You can even put the Logo plant on the golden color.
• "Frisette Plus"
• "Ação 3 em 1: Esfoliante, limpeza e hidratação"
• "Regeneração Celular"
• "Velvet Ritual"
• Logo of the company "Quelvia" (attached).
• Please, REMOVE the words "Produtos Naturais" from the logo.
• Elegance and show softness.
• Something that reminds of nature or fresh.
Should not have
• Strong colors or many images that distract the information.

```html
<!DOCTYPE html>
<html lang="pt">
<head>
<meta charset="utf-8">
<title>Quelvia – Frisette Plus label</title>
<link rel="stylesheet" href="https://fonts.googleapis.com/css2?family=Open+Sans:wght@400;600&family=Roboto+Condensed:ital,wght@0,400;1,400&display=swap">
<style>
  :root {
    --stage: #ececec;
    --label: #ffffff;
    --brand-green: #9bcb3c;
    --ink: #2b2b2b;
    --sage: #8a9a78;
    --bar-grey: #b5b5b5;
    --bar-lime: #c9dc2e;
    --bar-orange: #f4a62a;
    --gold-deep: #cfad3e;
    --gold-light: #efe07c;
    --white: #ffffff;
  }
  * { margin: 0; padding: 0; box-sizing: border-box; }
  html, body {
    width: 1200px; height: 800px; overflow: hidden;
    background: var(--stage);
  }
  .label {
    position: absolute;
    left: 420px; top: 30px;
    width: 359px; height: 740px;
    background: var(--label);
    overflow: hidden;
  }
  .texture {
    position: absolute; left: 0; top: 0; width: 100%; height: 520px;
    background: linear-gradient(170deg, rgba(220,220,220,0.3) 0%, rgba(255,255,255,0) 70%);
  }
  .brand {
    position: absolute; top: 140px; left: 0; width: 100%;
    display: flex; align-items: center; justify-content: center; gap: 10px;
  }
  .brand-dot {
    width: 34px; height: 34px; border-radius: 50%;
    background: linear-gradient(135deg, var(--gold-light), var(--gold-deep));
  }
  .brand-name {
    font-family: "Open Sans", sans-serif;
    font-weight: 600; font-size: 60px; line-height: 1;
    color: var(--brand-green);
    letter-spacing: -1px;
  }
  .product-name {
    position: absolute; right: 44px; top: 248px;
    font-family: "Roboto Condensed", sans-serif;
    font-style: italic; font-weight: 400; font-size: 33px; line-height: 1.2;
    color: var(--ink);
  }
  .claim {
    position: absolute; right: 40px; top: 355px;
    font-family: "Open Sans", sans-serif;
    font-weight: 600; font-size: 22px; line-height: 1.4; color: var(--sage);
  }
  .actions {
    position: absolute; left: 26px; right: 34px; top: 405px;
    display: flex; justify-content: space-between; list-style: none;
    font-family: "Roboto Condensed", sans-serif;
    font-size: 21px; line-height: 1.2; color: var(--sage);
  }
  .actions li { border-left: 5px solid; padding-left: 8px; }
  .actions .exfoliate { border-color: var(--bar-grey); }
  .actions .cleanse { border-color: var(--bar-lime); padding-left: 5px; }
  .actions .hydrate { border-color: var(--bar-orange); }
  .gold-band { position: absolute; left: 0; top: 0; width: 100%; height: 100%; }
  .band-text {
    position: absolute; right: 36px; top: 645px; text-align: right;
    font-family: "Open Sans", sans-serif;
    font-size: 20px; line-height: 1.25; color: var(--white);
  }
</style>
</head>
<body>
  <main class="label">
    <div class="texture" role="img" aria-label="Faint flowing fine-line pattern"></div>

    <svg class="gold-band" viewBox="0 0 359 740" aria-hidden="true">
      <defs>
        <linearGradient id="gold" x1="0" y1="0" x2="1" y2="1">
          <stop offset="0" stop-color="#cfad3e"/>
          <stop offset="1" stop-color="#efe07c"/>
        </linearGradient>
      </defs>
      <polygon points="0,681 359,482 359,740 0,740" fill="url(#gold)"/>
    </svg>

    <div class="brand">
      <span class="brand-dot"></span>
      <span class="brand-name">Quelvia</span>
    </div>

    <h1 class="product-name">Frisette Plus</h1>
    <p class="claim">Ação 3 em 1</p>
    <ul class="actions">
      <li class="exfoliate">Esfoliante</li>
      <li class="cleanse">Limpeza</li>
      <li class="hydrate">Hidratação</li>
    </ul>

    <p class="band-text">Regeneração Celular<br>Velvet Ritual</p>
  </main>
</body>
</html>
```